Business Card Design needed for start up company Halvora

In need of a new business card designed for a start up company based in Sydney, Halvora is a new start up innovative Company, our mission it to make property accessible for everyday Australian and to become the leading Real Estate platform in Australia. We want it to be fresh and clean.

Industry/Entity Type

Financial

Contact Information for Business Card

Section for Name
Section for Title

HALVORA - The Strength of Pooling
Mobile:
Direct:

Font styles to use
Sans Serif

Colors
33a6d7
0692cd
0255a3
ffffff

Requirements
Must have
• Logo, all business card details

```html
<!DOCTYPE html>
<html lang="en">
<head>
<meta charset="utf-8">
<title>Halvora Business Card</title>
<link href="https://fonts.googleapis.com/css2?family=Open+Sans:wght@400;600&display=swap" rel="stylesheet">
<style>
  :root {
    --stage: #3b3431;
    --card: #0c0c0d;
    --card-edge: #1c1c1e;
    --sky: #33a6d7;
    --cyan: #0692cd;
    --navy: #0255a3;
    --white: #ffffff;
    --silver: #b5b5b5;
    --muted: #d8d8d8;
    --divider: #222224;
  }
  * { box-sizing: border-box; margin: 0; padding: 0; }
  html, body {
    width: 1200px; height: 900px; overflow: hidden;
    background: var(--stage);
    font-family: "Open Sans", Arial, sans-serif;
  }
  .stage {
    width: 1200px; height: 900px;
    display: flex; align-items: center; justify-content: center; gap: 60px;
  }
  .card {
    width: 520px; height: 300px;
    background: var(--card);
    border: 1px solid var(--card-edge);
    box-shadow: 0 18px 40px rgba(0,0,0,.55);
  }

  /* front */
  .card-front { display: flex; }
  .front-brand {
    width: 50%; display: flex; align-items: center; justify-content: center;
  }
  .brand-name {
    font-weight: 600; font-size: 32px; letter-spacing: 1px; color: var(--navy);
  }
  .front-details {
    width: 50%; border-left: 1px solid var(--divider); padding: 58px 0 0 28px;
  }
  .person-name { color: var(--sky); font-size: 21px; font-weight: 600; line-height: 1.1; }
  .person-title { color: var(--white); font-size: 13px; margin-top: 2px; }
  .contacts { list-style: none; margin-top: 34px; }
  .contacts li {
    display: flex; align-items: center; gap: 12px;
    color: var(--muted); font-size: 14px; line-height: 1.5;
  }
  .contacts svg { width: 12px; height: 12px; fill: var(--cyan); flex: none; }

  /* back */
  .card-back {
    display: flex; flex-direction: column; align-items: center; justify-content: center;
  }
  .card-back .brand-name { color: var(--silver); font-size: 54px; letter-spacing: 2px; }
  .tagline {
    margin-top: 30px; color: var(--muted); font-size: 15px; letter-spacing: 1px;
  }
</style>
</head>
<body>
<main class="stage">
  <section class="card card-front" aria-label="Business card front">
    <div class="front-brand">
      <span class="brand-name">HALVORA</span>
    </div>
    <div class="front-details">
      <p class="person-name">Marcus Ellery</p>
      <p class="person-title">Managing Director</p>
      <ul class="contacts">
        <li><svg viewBox="0 0 12 12" aria-hidden="true"><path d="M2.5 0.5l2 2.5-1 1.2c.6 1.4 1.8 2.6 3.3 3.3l1.2-1 2.5 2-1 2C5 10.5 1.5 7 0.5 1.5z"/></svg>(061)-372-5148</li>
        <li><svg viewBox="0 0 12 12" aria-hidden="true"><path d="M2.5 0h7v12h-7zM3.8 1.3v8h4.4v-8z" fill-rule="evenodd"/></svg>042-618-3907</li>
        <li><svg viewBox="0 0 12 12" aria-hidden="true"><path d="M0 2h12v8H0zM1 3l5 3.5L11 3z" fill-rule="evenodd"/></svg>hello@halvora.co</li>
      </ul>
    </div>
  </section>
  <section class="card card-back" aria-label="Business card back">
    <span class="brand-name">HALVORA</span>
    <p class="tagline">THE STRENGTH OF POOLING</p>
  </section>
</main>
</body>
</html>
```